Trendy eye catching business card for lawn mowing business

Turf Tidy, a local community lawn mowing service, requires an eye catching trendy business card to drop into letterboxes.

We could simply throw something together from a Microsoft Word template, but we are wanting something more than this. Some other business’ images are attached for some inspiration.

We are requiring the card to have Turf Tidy with our slogan, Call The Brindles. In addition, provide details with that we are a local, affordable lawn mowing service, and for other gardening matters to simply just ask!
Plus the relevant contact details, phone, email, social media.

Target Market(s)

Local community members who require assistance with their garden care

Industry/Entity Type

Gardening

Contact Information for Business Card

the name TURF TIDY is our logo
telephone logo 0438 215 967
email logo turftidy@postbox-mail.example
Instagram logo turftidy
Facebook logo turftidy.sth
Lawn Mowing Service
Local Affordable
edge trim, blow and clipping removal included.
Other gardening matters, just ask!

Font styles to use
Serif
Sans Serif
Decorative
Script

Colors
9bcb3c
ffffff

Requirements
Must have
• All the details listed in Business Card Details.
Make these words prominent:
Turf Tidy
Lawn Mowing Service
Local
Affordable
Nice to have
• Our slogan ‘Call The Brindles’ incorporated.
Different colour background for front and reverse side
Greens, white and black colours
Subtle grass blades images incorporated
Should not have
• No images of lawnmowers.
No images of men/cartoons.
No using initials for Turf Tidy

```html
<!DOCTYPE html>
<html lang="en">
<head>
<meta charset="utf-8">
<title>Turf Tidy – Business Card</title>
<link href="https://fonts.googleapis.com/css2?family=Poppins:wght@400;500;700;800&display=swap" rel="stylesheet">
<style>
  :root {
    --page: #e4e4e4;
    --front-bg: #dfe9d4;
    --leaf: #3cb21a;
    --leaf-bright: #4fcc1f;
    --forest: #0d4a06;
    --forest-deep: #063000;
    --ink: #1f2a1a;
    --white: #ffffff;
  }
  * { box-sizing: border-box; margin: 0; padding: 0; }
  html, body { width: 1200px; height: 800px; overflow: hidden; }
  body {
    background: var(--page);
    font-family: "Poppins", sans-serif;
    position: relative;
  }
  .card {
    position: absolute;
    top: 245px;
    width: 540px;
    height: 310px;
    border-radius: 4px;
    overflow: hidden;
    box-shadow: 0 10px 24px rgba(0,0,0,.18);
  }

  /* Front */
  .card-front { left: 40px; background: var(--front-bg); }
  .brand {
    position: absolute;
    left: 34px; top: 112px;
    width: 200px;
    text-align: center;
  }
  .brand-name {
    font-weight: 800;
    font-size: 40px;
    line-height: 1;
    color: var(--forest);
    letter-spacing: 1px;
  }
  .brand-slogan {
    margin-top: 8px;
    font-weight: 500;
    font-size: 15px;
    color: var(--leaf);
  }
  .divider-vertical {
    position: absolute;
    left: 262px; top: 92px;
    width: 1px; height: 126px;
    background: var(--forest);
    opacity: .6;
  }
  .contact {
    position: absolute;
    left: 284px; top: 96px;
  }
  .contact-name {
    font-weight: 800;
    font-size: 21px;
    color: var(--forest);
    letter-spacing: .5px;
    margin-bottom: 10px;
  }
  .contact-list { list-style: none; }
  .contact-list li {
    display: flex;
    align-items: center;
    gap: 8px;
    font-size: 11.5px;
    color: var(--ink);
    line-height: 20px;
  }
  .contact-icon { width: 12px; height: 12px; flex: none; }
  .social-mark {
    width: 11px; height: 11px; flex: none;
    border-radius: 50%;
    background: var(--forest);
  }

  /* Back */
  .card-back {
    left: 620px;
    background: radial-gradient(ellipse at 45% 30%, #105a08 0%, var(--forest-deep) 75%);
  }
  .grass {
    position: absolute;
    left: 0; right: 0; bottom: 0;
    height: 150px;
    background: linear-gradient(180deg, rgba(60,178,26,0) 0%, var(--leaf) 40%, var(--leaf-bright) 100%);
  }
  .back-content {
    position: absolute;
    inset: 0;
    text-align: center;
    padding-top: 40px;
  }
  .service-title {
    font-weight: 800;
    font-size: 31px;
    line-height: 1.05;
    color: var(--leaf);
  }
  .service-tags {
    font-weight: 800;
    font-size: 26px;
    color: var(--leaf);
    margin-top: 2px;
  }
  .service-tags .sep { font-weight: 400; opacity: .7; margin: 0 6px; }
  .divider-short {
    width: 150px; height: 1px;
    background: var(--leaf);
    margin: 12px auto 14px;
  }
  .service-note {
    color: var(--white);
    font-weight: 500;
    font-size: 13.5px;
    line-height: 1.35;
  }
  .phone-big {
    margin-top: 26px;
    display: inline-flex;
    align-items: center;
    gap: 8px;
    font-weight: 800;
    font-size: 40px;
    color: var(--forest-deep);
  }
  .phone-big svg { width: 30px; height: 30px; }
</style>
</head>
<body>

<section class="card card-front" aria-label="Business card front">
  <div class="brand">
    <div class="brand-name">TURF<br>TIDY</div>
    <div class="brand-slogan">Call The Brindles</div>
  </div>
  <div class="divider-vertical"></div>
  <div class="contact">
    <div class="contact-name">NINA BRINDLE</div>
    <ul class="contact-list">
      <li>
        <svg class="contact-icon" viewBox="0 0 24 24"><path fill="#0d4a06" d="M6.6 10.8a15.1 15.1 0 0 0 6.6 6.6l2.2-2.2a1 1 0 0 1 1-.25 11.4 11.4 0 0 0 3.6.57 1 1 0 0 1 1 1V20a1 1 0 0 1-1 1A17 17 0 0 1 3 4a1 1 0 0 1 1-1h3.5a1 1 0 0 1 1 1c0 1.25.2 2.45.57 3.57a1 1 0 0 1-.25 1z"/></svg>
        0438 215 967
      </li>
      <li>
        <svg class="contact-icon" viewBox="0 0 24 24"><rect x="2" y="5" width="20" height="14" rx="2" fill="#0d4a06"/><path d="M3 6l9 7 9-7" fill="none" stroke="#dfe9d4" stroke-width="1.8"/></svg>
        turftidy@postbox-mail.example
      </li>
      <li><span class="social-mark"></span>turftidy.sth</li>
      <li><span class="social-mark"></span>turftidy</li>
    </ul>
  </div>
</section>

<section class="card card-back" aria-label="Business card back">
  <div class="grass" role="img" aria-label="Silhouette of grass blades along the bottom of the card"></div>
  <div class="back-content">
    <h1 class="service-title">LAWN MOWING SERVICE</h1>
    <div class="service-tags">LOCAL<span class="sep">|</span>AFFORDABLE</div>
    <div class="divider-short"></div>
    <p class="service-note">Edge trim, blow &amp; clipping removal included.<br>Other gardening matters, just ask!</p>
    <div class="phone-big">
      <svg viewBox="0 0 24 24"><path fill="#063000" d="M6.6 10.8a15.1 15.1 0 0 0 6.6 6.6l2.2-2.2a1 1 0 0 1 1-.25 11.4 11.4 0 0 0 3.6.57 1 1 0 0 1 1 1V20a1 1 0 0 1-1 1A17 17 0 0 1 3 4a1 1 0 0 1 1-1h3.5a1 1 0 0 1 1 1c0 1.25.2 2.45.57 3.57a1 1 0 0 1-.25 1z"/></svg>
      0438 215 967
    </div>
  </div>
</section>

</body>
</html>
```